Tolbek cards

I want a simple business card that pops.
Logo on one side.
On side two i want.
"Are you thinking about a new building on your property, or renovating an existing structure? Contact".....
Owners Name: Dale Whitacre
Owners Phone number: 610-555-0187
Address:4076 Copper Ridge RD, Bedford, PA 15522
Committed to Quality, Service, and Integrity

```html
<!DOCTYPE html>
<html lang="en">
<head>
<meta charset="utf-8">
<title>Tolbek Builders – Business Card</title>
<link href="https://fonts.googleapis.com/css2?family=Montserrat:wght@700&family=Poppins:wght@400&display=swap" rel="stylesheet">
<style>
  :root {
    --bg: #adadad;
    --brown: #402c1b;
    --white: #ffffff;
    --head-font: "Montserrat", sans-serif;
    --body-font: "Poppins", sans-serif;
  }
  * { margin: 0; padding: 0; box-sizing: border-box; }
  html, body { width: 1093px; height: 1200px; overflow: hidden; }
  body { background: var(--bg); position: relative; }

  .card {
    position: absolute;
    left: 265px;
    width: 578px;
    height: 356px;
    border-radius: 26px;
    overflow: hidden;
  }
  .card--back { top: 226px; background: var(--brown); color: var(--white); }
  .card--front { top: 621px; background: var(--white); }

  .pitch {
    position: absolute;
    top: 41px; left: 0; right: 0;
    text-align: center;
    font-family: var(--head-font);
    font-weight: 700;
    font-size: 21.5px;
    line-height: 29px;
    letter-spacing: -0.3px;
  }

  .divider-label {
    position: absolute;
    top: 150px; left: 28px; right: 26px;
    display: flex; align-items: center; gap: 8px;
    font-family: var(--body-font);
    font-size: 16.5px;
  }
  .divider-label .rule { flex: 1; height: 1px; background: var(--white); position: relative; }
  .divider-label .rule--left::after,
  .divider-label .rule--right::before {
    content: ""; position: absolute; top: -2px;
    width: 5px; height: 5px; border-radius: 50%; background: var(--white);
  }
  .divider-label .rule--left::after { right: -2px; }
  .divider-label .rule--right::before { left: -2px; }

  .owner-name {
    position: absolute; top: 197px; left: 0; right: 0;
    text-align: center;
    font-family: var(--head-font); font-weight: 700; font-size: 22px;
  }
  .owner-phone, .owner-address, .tagline {
    position: absolute; left: 0; right: 0; text-align: center;
    font-family: var(--body-font); font-size: 16.5px;
  }
  .owner-phone { top: 227px; }
  .short-rule {
    position: absolute; top: 260px; left: 270px;
    width: 38px; height: 1px; background: var(--white);
  }
  .owner-address { top: 273px; }
  .long-rule {
    position: absolute; top: 308px; left: 25px; right: 25px;
    height: 1px; background: var(--white);
  }
  .tagline { top: 314px; }

  .brand {
    position: absolute; top: 128px; left: 0; right: 0;
    display: flex; align-items: center; justify-content: center; gap: 16px;
    color: var(--brown);
    font-family: var(--head-font); font-weight: 700;
  }
  .brand-mark { width: 62px; height: 62px; background: var(--brown); }
  .brand-name { line-height: 1; }
  .brand-name .primary { display: block; font-size: 56px; letter-spacing: -1px; }
  .brand-name .secondary { display: block; font-size: 19px; letter-spacing: 0.5px; margin-top: 2px; }
</style>
</head>
<body>
  <section class="card card--back">
    <h1 class="pitch">ARE YOU THINKING ABOUT A NEW BUILDING<br>ON YOUR PROPERTY, OR<br>RENOVATING AN EXISTING STRUCTURE?</h1>
    <div class="divider-label">
      <span class="rule rule--left"></span>
      <span>Contact</span>
      <span class="rule rule--right"></span>
    </div>
    <p class="owner-name">DALE WHITACRE</p>
    <p class="owner-phone">610-555-0187</p>
    <span class="short-rule"></span>
    <p class="owner-address">4076 Copper Ridge RD, Bedford, PA 15522</p>
    <span class="long-rule"></span>
    <p class="tagline">Committed to Quality, Service and Integrity</p>
  </section>

  <section class="card card--front">
    <div class="brand">
      <span class="brand-mark"></span>
      <p class="brand-name">
        <span class="primary">TOLBEK</span>
        <span class="secondary">BUILDERS LLC</span>
      </p>
    </div>
  </section>
</body>
</html>
```